Verlindo Magician

I want the business card for my business to give to people who watch that later I will be employed to show magic here is my website http://www.balsamomagicien.com/I want the interesting design , i am very opened for formal and informal, I watch a lot of design so don't stick to the common shape and form but i hope it can also be produced the thing to write on will be the same as in picture that i will upload , i also will upload the logo for you that so can be easy to useDenis CostilleMagicianMAGICIAN BALSAMO 17 rue des Tilleuls - 25000 BESANÇON contact@verlindoillusions.example tel. 0381 946 157 tel. 0674 219 503

```html
<!DOCTYPE html>
<html lang="fr">
<head>
<meta charset="utf-8">
<title>Verlindo Magician – Business Card</title>
<link href="https://fonts.googleapis.com/css2?family=Jost:wght@400;500&display=swap" rel="stylesheet">
<style>
  :root {
    --page-bg: #d8d4d0;
    --card-bg: #f2f1ef;
    --ink: #1c1c1c;
    --accent-red: #b3121a;
    --band-bg: #161616;
    --band-text: #c9c9c9;
    --portrait-dark: #2b2b2b;
    --portrait-mid: #6a6a6a;
  }
  * { margin: 0; padding: 0; box-sizing: border-box; }
  html, body {
    width: 1200px; height: 969px; overflow: hidden;
    background: var(--page-bg);
    font-family: "Jost", "Futura", sans-serif;
  }
  .business-card {
    position: absolute;
    left: 100px; top: 199px;
    width: 1000px; height: 571px;
    background: var(--card-bg);
    box-shadow: 0 10px 30px rgba(0,0,0,0.12);
    overflow: hidden;
  }
  .portrait-area {
    position: absolute;
    left: 166px; top: 157px;
    width: 164px; height: 209px;
    background: linear-gradient(180deg, var(--portrait-mid) 0%, var(--portrait-dark) 55%);
    border-radius: 60px 60px 6px 6px;
  }
  .brand-name {
    position: absolute;
    left: 148px; top: 366px;
    width: 200px;
    text-align: center;
    color: var(--ink);
    font-weight: 400;
    font-size: 32px;
    line-height: 1;
    letter-spacing: 0.5px;
  }
  .brand-name .brand-sub {
    display: block;
    font-size: 12px;
    letter-spacing: 2px;
    margin-top: 6px;
  }
  .contact-block {
    position: absolute;
    left: 409px; top: 150px;
    color: var(--ink);
  }
  .person-name { font-size: 35px; font-weight: 400; line-height: 1.1; }
  .person-role { font-size: 25px; color: var(--accent-red); line-height: 1.1; margin-bottom: 22px; }
  .company-line, .address-line { font-size: 23px; line-height: 30px; }
  .contact-list { list-style: none; margin-top: 12px; }
  .contact-list li {
    display: flex; align-items: center;
    font-size: 22px; line-height: 33px;
  }
  .contact-list svg { width: 20px; height: 20px; margin-right: 14px; fill: var(--ink); flex: none; }
  .web-band {
    position: absolute;
    left: 0; top: 484px;
    width: 100%; height: 43px;
    background: var(--band-bg);
    display: flex; align-items: center; justify-content: center;
    gap: 16px;
  }
  .web-address {
    color: var(--band-text);
    font-size: 21px;
    letter-spacing: 6px;
  }
  .suit-pair { display: flex; gap: 3px; }
  .suit-pair svg { width: 14px; height: 14px; fill: var(--accent-red); }
</style>
</head>
<body>
  <div class="business-card">
    <div class="portrait-area" role="img" aria-label="Illustrated portrait of the magician holding a playing card"></div>
    <div class="brand-name">VERLINDO<span class="brand-sub">MAGICIAN</span></div>

    <div class="contact-block">
      <h1 class="person-name">Marc Ravoulet</h1>
      <p class="person-role">Magician</p>
      <p class="company-line">MAGICIAN VERLINDO</p>
      <p class="address-line">17 rue des Tilleuls - 25000 BESANÇON</p>
      <ul class="contact-list">
        <li>
          <svg viewBox="0 0 24 24" aria-hidden="true"><path d="M6.6 10.8a15.1 15.1 0 0 0 6.6 6.6l2.2-2.2a1 1 0 0 1 1-.25 11.4 11.4 0 0 0 3.6.57 1 1 0 0 1 1 1V20a1 1 0 0 1-1 1A17 17 0 0 1 3 4a1 1 0 0 1 1-1h3.5a1 1 0 0 1 1 1c0 1.25.2 2.45.57 3.6a1 1 0 0 1-.25 1z"/></svg>
          0381 946 157
        </li>
        <li>
          <svg viewBox="0 0 24 24" aria-hidden="true"><path d="M6.6 10.8a15.1 15.1 0 0 0 6.6 6.6l2.2-2.2a1 1 0 0 1 1-.25 11.4 11.4 0 0 0 3.6.57 1 1 0 0 1 1 1V20a1 1 0 0 1-1 1A17 17 0 0 1 3 4a1 1 0 0 1 1-1h3.5a1 1 0 0 1 1 1c0 1.25.2 2.45.57 3.6a1 1 0 0 1-.25 1z"/></svg>
          0674 219 503
        </li>
        <li>
          <svg viewBox="0 0 24 24" aria-hidden="true"><path d="M3 6h18v12H3z M3 6l9 7 9-7" fill="none" stroke="#1c1c1c" stroke-width="2"/><path d="M3 6h18l-9 7z"/></svg>
          contact@verlindoillusions.example
        </li>
      </ul>
    </div>

    <div class="web-band">
      <span class="suit-pair" aria-hidden="true">
        <svg viewBox="0 0 20 20"><path d="M10 1C7 6 2 8 2 12a4 4 0 0 0 7 2.5L8 19h4l-1-4.5A4 4 0 0 0 18 12c0-4-5-6-8-11z"/></svg>
        <svg viewBox="0 0 20 20"><path d="M10 1l7 9-7 9-7-9z"/></svg>
      </span>
      <span class="web-address">www.verlindoillusions.example</span>
      <span class="suit-pair" aria-hidden="true">
        <svg viewBox="0 0 20 20"><path d="M10 18C4 13 1 10 1 6.5A4.5 4.5 0 0 1 10 4a4.5 4.5 0 0 1 9 2.5C19 10 16 13 10 18z"/></svg>
        <svg viewBox="0 0 20 20"><circle cx="10" cy="5.5" r="4"/><circle cx="5" cy="11" r="4"/><circle cx="15" cy="11" r="4"/><path d="M9 11h2l1.5 8h-5z"/></svg>
      </span>
    </div>
  </div>
</body>
</html>
```